Coastline Premier Retreats Business Card Design

Design a business card for Coastline Premier Retreats. Look at the website for colors and reference. Card should have logo, name, title, office number, mobile number, email, URL and a tagline like, "Luxury Hotel & Resort Email Marketing" (This might change).

https://www.coastlinepremierretreats.example

The rest I will leave up to your imagination.

Contact Information for Business Card

Logo, name, title, office number, mobile number, email, URL and a tagline like, "Luxury Hotel & Resort Email Marketing" (This might change).

```html
<!DOCTYPE html>
<html lang="en">
<head>
<meta charset="utf-8">
<title>Coastline Premier Retreats – Business Card</title>
<link href="https://fonts.googleapis.com/css2?family=Montserrat:wght@400;500;700&display=swap" rel="stylesheet">
<style>
  :root {
    --backdrop: #101011;
    --card: #1d1d1e;
    --accent: #f07a1e;
    --ink: #f2f2f2;
    --ink-soft: #e4e4e4;
  }
  * { box-sizing: border-box; margin: 0; padding: 0; }
  html, body {
    width: 900px;
    height: 1200px;
    overflow: hidden;
    background: var(--backdrop);
    font-family: "Montserrat", Arial, sans-serif;
  }
  .canvas {
    position: relative;
    width: 900px;
    height: 1200px;
  }
  .card {
    position: absolute;
    left: 135px;
    width: 630px;
    height: 357px;
    background: var(--card);
  }
  .card--front { top: 215px; }
  .card--back { top: 628px; }

  /* Front: company name */
  .brand {
    position: absolute;
    left: 0; right: 0;
    top: 128px;
    text-align: center;
    color: var(--ink);
    font-weight: 700;
  }
  .brand__primary {
    display: block;
    font-size: 46px;
    line-height: 1;
    letter-spacing: 1px;
  }
  .brand__secondary {
    display: block;
    margin-top: 8px;
    font-size: 17px;
    letter-spacing: 5px;
  }

  /* Back: contact details */
  .frame {
    position: absolute;
    left: 39px;
    top: 33px;
    width: 552px;
    height: 291px;
    border: 3px solid var(--accent);
  }
  .contact {
    position: absolute;
    left: 0; right: 0;
    top: 50px;
    text-align: center;
  }
  .contact__name {
    color: var(--accent);
    font-weight: 700;
    font-size: 24px;
    letter-spacing: 0.5px;
    line-height: 1.2;
  }
  .contact__title {
    color: var(--ink-soft);
    font-weight: 400;
    font-size: 17px;
    letter-spacing: 0.8px;
    margin-top: 2px;
  }
  .contact__rule {
    width: 93px;
    height: 3px;
    background: var(--accent);
    margin: 9px auto 0;
  }
  .contact__list {
    list-style: none;
    margin-top: 26px;
    color: var(--ink-soft);
    font-weight: 400;
  }
  .contact__list li { line-height: 26px; font-size: 16px; letter-spacing: 0.6px; }
  .contact__list .phone { font-size: 17px; letter-spacing: 3px; }
  .tagline {
    position: absolute;
    left: 50%;
    bottom: -11px;
    transform: translateX(-50%);
    padding: 0 11px;
    background: var(--card);
    color: var(--ink);
    font-size: 15px;
    font-weight: 500;
    white-space: nowrap;
    line-height: 18px;
  }
</style>
</head>
<body>
<main class="canvas">
  <section class="card card--front" aria-label="Card front">
    <h1 class="brand">
      <span class="brand__primary">COASTLINE</span>
      <span class="brand__secondary">PREMIER RETREATS</span>
    </h1>
  </section>

  <section class="card card--back" aria-label="Card back">
    <div class="frame">
      <div class="contact">
        <h2 class="contact__name">DANA KERROW</h2>
        <p class="contact__title">President</p>
        <div class="contact__rule"></div>
        <ul class="contact__list">
          <li class="phone">808.555.0142</li>
          <li class="phone">561.555.0190</li>
          <li>info@coastlinepremierretreats.example</li>
          <li>www.coastlinepremierretreats.example</li>
        </ul>
      </div>
      <p class="tagline">Luxury Hotel &amp; Resort Email Marketing</p>
    </div>
  </section>
</main>
</body>
</html>
```